Home Baker of cakes, muffins, cookies and pastries.

I am looking for business cards for my home baking business called " Yum Bea-A Treat " - I want them to be super cute and girly, yet simple and modern at the same time. Pastel colours is what I envision with the main colour being baby pink.

```html
<!DOCTYPE html>
<html lang="en">
<head>
<meta charset="utf-8">
<title>Yum Bea-A Treat — Business Cards</title>
<link href="https://fonts.googleapis.com/css2?family=Lato:wght@400;700&family=Dancing+Script:wght@600&display=swap" rel="stylesheet">
<style>
  :root {
    --page: #e9e7e8;
    --pink: #ea87a6;
    --pink-light: #f09ab5;
    --pink-deep: #e57598;
    --white: #ffffff;
    --aqua: #8fd3d6;
    --shadow: rgba(60, 30, 40, 0.22);
  }
  * { margin: 0; padding: 0; box-sizing: border-box; }
  html, body {
    width: 1200px; height: 900px; overflow: hidden;
    background: var(--page);
    font-family: "Lato", Arial, sans-serif;
  }
  .canvas { position: relative; width: 1200px; height: 900px; }

  .card {
    position: absolute;
    width: 560px; height: 320px;
    border-radius: 18px;
    overflow: hidden;
    box-shadow: 0 14px 30px var(--shadow);
  }

  /* Contact side */
  .card--contact {
    left: 80px; top: 110px;
    background: linear-gradient(135deg, var(--pink-deep), var(--pink-light));
    color: var(--white);
  }
  .brand {
    position: absolute; left: 0; right: 0; top: 70px;
    display: flex; align-items: center; justify-content: center; gap: 12px;
  }
  .brand__dot {
    width: 16px; height: 16px; border-radius: 50%;
    background: var(--white);
  }
  .brand__name {
    font-family: "Lato", Arial, sans-serif;
    font-weight: 700;
    font-size: 34px;
    letter-spacing: 1px;
    color: var(--white);
  }
  .owner {
    position: absolute; right: 40px; top: 150px; text-align: right;
  }
  .owner__name {
    font-family: "Dancing Script", cursive;
    font-size: 28px; font-weight: 600;
  }
  .owner__role { font-size: 12px; letter-spacing: 0.5px; margin-top: -2px; }
  .contact-list {
    position: absolute; left: 36px; bottom: 34px;
    list-style: none; font-size: 13px; line-height: 22px;
  }
  .contact-list li { display: flex; align-items: center; gap: 10px; }
  .contact-list svg { width: 13px; height: 13px; flex: none; }
  .contact-list .no-icon { padding-left: 23px; }

  /* Logo side */
  .card--logo {
    left: 560px; top: 470px;
    background: repeating-linear-gradient(
      -60deg,
      var(--pink) 0 26px,
      var(--white) 26px 40px
    );
  }
  .label {
    position: absolute; left: 90px; top: 60px;
    width: 380px; height: 200px;
  }
  .label svg { position: absolute; inset: 0; }
  .label__content {
    position: absolute; inset: 0;
    display: flex; flex-direction: column; align-items: center; justify-content: center;
  }
  .label__brand {
    display: flex; align-items: center; gap: 10px;
  }
  .label__dot { width: 14px; height: 14px; border-radius: 50%; background: var(--pink); }
  .label__name {
    font-weight: 700; font-size: 32px; color: var(--pink);
    letter-spacing: 1px;
  }
  .label__rule {
    width: 250px; height: 2px; background: var(--aqua);
    margin: 12px 0 10px;
  }
  .label__web {
    font-size: 13px; letter-spacing: 3px; color: var(--pink-deep);
  }
</style>
</head>
<body>
<main class="canvas">

  <section class="card card--contact" aria-label="Business card, contact side">
    <div class="brand">
      <span class="brand__dot"></span>
      <span class="brand__name">Yum Bea-A Treat</span>
    </div>
    <div class="owner">
      <div class="owner__name">Marisol Penhart</div>
      <div class="owner__role">Owner / Founder</div>
    </div>
    <ul class="contact-list">
      <li>
        <svg viewBox="0 0 16 16" aria-hidden="true"><path fill="#fff" d="M3 1l3 3-1.5 2a9 9 0 0 0 5.5 5.5L12 10l3 3-2 2C7 15 1 9 1 3z"/></svg>
        555.204.3189
      </li>
      <li>
        <svg viewBox="0 0 16 16" aria-hidden="true"><rect x="1" y="3" width="14" height="10" rx="1" fill="#fff"/><path d="M1.5 3.5L8 9l6.5-5.5" stroke="#e57598" stroke-width="1.4" fill="none"/></svg>
        mpenhart@yumbea-atreat.com
      </li>
      <li class="no-icon">42 Maple Orchard Ln, Fairview, IN - 40000</li>
    </ul>
  </section>

  <section class="card card--logo" aria-label="Business card, logo side">
    <div class="label">
      <svg viewBox="0 0 380 200" aria-hidden="true">
        <path fill="#fff" d="M40 10 H340 Q340 30 360 30 Q370 30 370 50 V150 Q370 170 360 170 Q340 170 340 190 H40 Q40 170 20 170 Q10 170 10 150 V50 Q10 30 20 30 Q40 30 40 10 Z"/>
      </svg>
      <div class="label__content">
        <div class="label__brand">
          <span class="label__dot"></span>
          <span class="label__name">Yum Bea-A Treat</span>
        </div>
        <div class="label__rule"></div>
        <div class="label__web">www.yumbea-atreat.com</div>
      </div>
    </div>
  </section>

</main>
</body>
</html>
```